Life Coaching Business Needs A Business card Design

Earthy, quirky, colourful business card needed for a Life Coaching company supporting same sex attracted young men. My coaching supports these same sex attracted guys to find their own inner happiness and passion and purpose and not feel they need to live a 'label' or follow the crowd. It its about personal passion and happiness.
IT IS ABOUT THEIR INNER RAINBOW.
Some aspects of rainbow would be important to the design.

I have uploaded a recently designed POSTCARD and the business card will be a smaller version with much less information. The Business Card will take the very important parts of the POSTCARD

Front of Card.......
I'm thinking the front of the card would need to be the large LOGO with a rainbow emerging from the inside...from the heart...the core. This will almost FILL the front of the card. This has been uploaded for you. IMMEDIATELY under the LOGO ( to make it a part of the logo) would be the words COACHING * WELLNESS *
The statement HAPPINESS and WHOLENESS for MEN WHO DATE MEN should feature across the front of the BUSINESS CARD as it does across the back of the POSTCARD. It will need some kind of rainbow background to the statement as it does on the POSTCARD. Needs to be a different rainbow pattern. See what you think.

That could be the front. On a black background.
I wonder what you think and what you will do with that.

Back Of Card.

I'm hoping the back of the BUSINESS card could be the PHOTO section from the back of the POSTCARD. The photo and the quote. I will make the quote shorter to fit better on a BUSINESS card. It can be written in a handwriting style to make it look like a personal message from me as it is on the POSTCARD.

All across the top of the back of the card could be the statement
MOTIVATION and INSPIRATION for MEN WHO DATE MEN

Across the card under the statement would be the three contacts
www.brightvolume.com *0437 615 203*tom@brightvolume.com

It would be great to see if you have a different idea for this arrangement.

At the bottom of the Business card ( as on the photo at on the POSTCARD ) would be my name with a description underneath

Tom Walbrook
Transformational Life Coach * Happiness Guru * Change catalyst

What do you think ? Will all of this work ?
I hope I haven't been too prescriptive. I don't want this to be a boring job for you.

Looking forward to hearing what you think and seeing what you come up with.

Target Market(s)

Same sex attracted males. All ages. Especially those who are struggling or unhappy or depressed. The card must be uplifting and it must SPEAK to these guys. I want ti include a personal 'quote' from me ( in handwriting font as if I wrote to them ) to encourage these guys to get the help they need.

Industry/Entity Type

Business

Contact Information for Business Card

I have been quite prescriptive but am happy to see what the designer might come up with as well. I don't mean to make it boring for the designer. I have included names and contact details in the brief. Please let me know if I need to give you more details.

Requirements
Must have
• LOGO
• A clear statement on the front and back to state clearly who the coaching service is for. I have explained these in the brief.
• Pic of me to fill the back of the card with room to write the details on. I have other pics if needed.
• Needs to be casual and inviting. Almost informal and organic. Quite earthy to balance with the 'lifestyle' these guys can often live.
Nice to have
• Colour and ideas to keep it uncluttered.
Should not have
• Formal design or 'business' like feel.

```html
<!DOCTYPE html>
<html lang="en">
<head>
<meta charset="utf-8">
<title>Bright Volume – Business Card Front</title>
<link rel="stylesheet" href="https://fonts.googleapis.com/css2?family=Montserrat:wght@600;800&family=Marcellus&display=swap">
<style>
  :root {
    --backdrop: #2a2b2d;
    --card: #1b1b1b;
    --panel: #000000;
    --white: #ffffff;
    --figure-light: #f2f2f2;
    --figure-mid: #c9c9c9;
    --ink-outline: #1c1c1c;
    --rb-pink: #e8357d;
    --rb-violet: #3a2a86;
    --rb-lilac: #6c5aa6;
    --rb-blue: #1d7cc4;
    --rb-teal: #19a3a0;
    --rb-green: #6cb52d;
    --rb-yellow: #f3d21a;
    --rb-orange: #ef8a1c;
    --rb-red: #d7261f;
  }
  html, body {
    margin: 0;
    padding: 0;
    width: 1200px;
    height: 900px;
    overflow: hidden;
    background: var(--backdrop);
  }
  .canvas {
    position: relative;
    width: 1200px;
    height: 900px;
  }
  .card {
    position: absolute;
    left: 70px;
    top: 122px;
    width: 1063px;
    height: 635px;
    background: var(--card);
    border-radius: 10px 30px 30px 10px;
    overflow: hidden;
  }
  .brand-panel {
    position: absolute;
    left: 185px;
    top: 23px;
    width: 698px;
    height: 435px;
    background: var(--panel);
  }
  .hero-illustration {
    position: absolute;
    left: 145px;
    top: 35px;
    width: 420px;
    height: 292px;
    border-radius: 46% 46% 10% 10% / 40% 40% 8% 8%;
    background:
      linear-gradient(125deg,
        var(--figure-light) 0%,
        var(--figure-mid) 45%,
        var(--rb-pink) 62%,
        var(--rb-orange) 70%,
        var(--rb-green) 80%,
        var(--rb-blue) 92%,
        var(--figure-light) 100%);
    opacity: 0.85;
  }
  .brand-name {
    position: absolute;
    left: 0;
    right: 0;
    bottom: 40px;
    margin: 0;
    text-align: center;
    font-family: "Montserrat", sans-serif;
    font-weight: 600;
    font-size: 71px;
    line-height: 1;
    letter-spacing: 1px;
    color: var(--white);
    text-transform: uppercase;
  }
  .brand-tagline {
    position: absolute;
    left: 185px;
    width: 698px;
    top: 432px;
    margin: 0;
    text-align: center;
    font-family: "Marcellus", serif;
    font-size: 38px;
    letter-spacing: 2px;
    word-spacing: 14px;
    color: var(--white);
    padding-left: 66px;
    box-sizing: border-box;
  }
  .audience-band {
    position: absolute;
    left: 0;
    top: 511px;
    width: 100%;
    height: 77px;
    background: linear-gradient(90deg,
      var(--rb-violet) 0%,
      var(--rb-lilac) 10%,
      var(--rb-blue) 24%,
      var(--rb-teal) 40%,
      var(--rb-green) 50%,
      var(--rb-yellow) 62%,
      var(--rb-orange) 80%,
      var(--rb-red) 100%);
    display: flex;
    align-items: center;
    justify-content: center;
  }
  .audience-statement {
    margin: 0;
    font-family: "Montserrat", sans-serif;
    font-weight: 800;
    font-size: 31.5px;
    color: var(--white);
    text-transform: uppercase;
    letter-spacing: 0.2px;
    white-space: nowrap;
    text-shadow:
      2px 0 0 var(--ink-outline), -2px 0 0 var(--ink-outline),
      0 2px 0 var(--ink-outline), 0 -2px 0 var(--ink-outline),
      1.5px 1.5px 0 var(--ink-outline), -1.5px -1.5px 0 var(--ink-outline),
      1.5px -1.5px 0 var(--ink-outline), -1.5px 1.5px 0 var(--ink-outline);
  }
</style>
</head>
<body>
  <main class="canvas">
    <section class="card" aria-label="Business card front">
      <div class="brand-panel">
        <div class="hero-illustration" role="img" aria-label="Illustration of a white silhouette of a man with arms raised wide, a rainbow of ribbons streaming from his chest"></div>
        <h1 class="brand-name">Bright Volume</h1>
      </div>
      <p class="brand-tagline">COACHING WELLNESS</p>
      <div class="audience-band">
        <p class="audience-statement">Happiness and Wholeness for Men Who Date Men</p>
      </div>
    </section>
  </main>
</body>
</html>
```